Moravel Aesthetic Doctor

I require an elegant, luxurious looking business card for my aesthetic business. I am a doctor and that will set me aside from competitors. I am planning to provide home and spa based treatments to clients with high expectations. I have attached my logo.

```html
<!DOCTYPE html>
<html lang="en">
<head>
<meta charset="UTF-8">
<title>Moravel Aesthetic Doctor – Business Card</title>
<link href="https://fonts.googleapis.com/css2?family=Roboto:wght@300;400;500&display=swap" rel="stylesheet">
<style>
  :root {
    --backdrop: #3b3b3d;
    --card: #1f2022;
    --card-edge: #2a2b2e;
    --sky: #5ab7ea;
    --silver: #c4ced8;
    --ink: #1b1c1e;
    --white: #f4f6f8;
    --rule: #8b929a;
  }
  * { margin: 0; padding: 0; box-sizing: border-box; }
  html, body {
    width: 799px; height: 1200px; overflow: hidden;
    background: var(--backdrop);
    font-family: "Roboto", Arial, sans-serif;
  }
  .card {
    position: absolute; left: 50px;
    width: 700px; height: 400px;
    background: linear-gradient(160deg, var(--card-edge), var(--card) 60%);
    box-shadow: 0 10px 30px rgba(0,0,0,.45);
    overflow: hidden;
  }
  .card--front { top: 130px; }
  .card--back { top: 670px; }

  .brand {
    position: absolute; display: flex; align-items: center; gap: 18px;
  }
  .brand__mark {
    width: 92px; height: 92px; border-radius: 50%;
    border: 3px solid var(--silver);
  }
  .brand__name {
    color: var(--silver); font-weight: 300; font-size: 44px;
    line-height: 1; letter-spacing: 1px;
  }
  .card--front .brand { left: 150px; top: 52px; }
  .card--back .brand { left: 140px; top: 40px; }

  .services {
    position: absolute; left: 0; right: 0; top: 198px;
    text-align: center; color: var(--white);
    font-size: 19px; line-height: 27px;
  }
  .band-tagline {
    position: absolute; left: 0; right: 0; top: 268px; height: 42px;
    background: var(--sky); color: var(--ink);
    font-size: 20px; letter-spacing: 1px;
    display: flex; align-items: center; justify-content: center;
  }

  .side-strip {
    position: absolute; left: 0; top: 0; bottom: 0; width: 46px;
    background: var(--sky);
  }
  .side-rule {
    position: absolute; left: 54px; top: 0; bottom: 0; width: 3px;
    background: var(--rule);
  }
  .doctor {
    position: absolute; left: 90px; top: 178px; width: 450px;
    border-bottom: 1px solid var(--rule); padding-bottom: 6px;
  }
  .doctor__name { color: var(--rule); font-size: 27px; font-weight: 300; }
  .doctor__letters { color: var(--sky); font-size: 13px; margin-left: 4px; }
  .doctor__diploma { color: var(--sky); font-size: 17px; margin-top: 2px; }

  .contacts { position: absolute; left: 90px; top: 262px; color: var(--silver); font-size: 17px; }
  .contact { display: flex; align-items: center; gap: 10px; height: 36px; }
  .contact svg { width: 24px; height: 24px; flex: none; }

  .band-social {
    position: absolute; right: 0; top: 322px; width: 200px; height: 30px;
    background: var(--sky);
    display: flex; align-items: center; padding-left: 14px; gap: 8px;
  }
  .social-dot { width: 22px; height: 22px; border-radius: 50%; background: var(--white); }
</style>
</head>
<body>

<section class="card card--front">
  <div class="brand">
    <div class="brand__mark"></div>
    <div class="brand__name">Moravel Aesthetic Doctor</div>
  </div>
  <div class="services">
    <p>Dermal Injectables &nbsp;|&nbsp; Plasma Facials &nbsp;|&nbsp; Microneedling</p>
    <p>Skin Boosters &nbsp;|&nbsp; Excessive Sweating</p>
  </div>
  <div class="band-tagline">HOME AND SPA BASED TREATMENTS</div>
</section>

<section class="card card--back">
  <div class="side-strip"></div>
  <div class="side-rule"></div>
  <div class="brand">
    <div class="brand__mark"></div>
    <div class="brand__name">Moravel Aesthetic Doctor</div>
  </div>
  <div class="doctor">
    <p><span class="doctor__name">Dr Elena Varsk</span><span class="doctor__letters">MRCPCH MD</span></p>
    <p class="doctor__diploma">Australasian Diploma of Aesthetic Medicine</p>
  </div>
  <div class="contacts">
    <div class="contact">
      <svg viewBox="0 0 24 24" fill="none" stroke="#c4ced8" stroke-width="1.5"><circle cx="12" cy="12" r="11"/><path d="M8 6.5l2 2.5-1.2 1.5c.8 1.8 2 3 3.7 3.7l1.5-1.2 2.5 2-1.2 2c-4.5-.5-8.5-4.5-9-9z" fill="#c4ced8" stroke="none"/></svg>
      <span>0800 454 318</span>
    </div>
    <div class="contact">
      <svg viewBox="0 0 24 24" fill="none" stroke="#c4ced8" stroke-width="1.5"><circle cx="12" cy="12" r="11"/><rect x="6" y="8" width="12" height="8"/><path d="M6 8l6 5 6-5"/></svg>
      <span>elena@moravel.co.nz</span>
    </div>
    <div class="contact">
      <svg viewBox="0 0 24 24" fill="none" stroke="#c4ced8" stroke-width="1.5"><circle cx="12" cy="12" r="11"/><circle cx="12" cy="12" r="6"/><path d="M6 12h12M12 6c-2.5 3-2.5 9 0 12M12 6c2.5 3 2.5 9 0 12"/></svg>
      <span>www.moravel.co.nz</span>
    </div>
  </div>
  <div class="band-social">
    <span class="social-dot"></span>
    <span class="social-dot"></span>
  </div>
</section>

</body>
</html>
```